WP website design (Harrowgate)

We need a wordpress design for an established auction and real estate company based in Florida. The winning design will incorporate a professional color scheme with company logo in a clean layout. The design needs to consider that this will be developed on a responsive theme. Colors are those that will highlight the logo.

Industry/Entity Type

Real Estate

Font styles to use
Serif
Sans Serif

Colors

Designer to choose colors to be used in the design.

Requirements
Must have
• Navigation:
1) Home
2) Auctions
3) Online Auctions
4) About Us
5) Services
6) Real Estate Listings
7) References
8) Contact Us

Colors will be blue (#000066) / red (#B10000) and black or other complementary color. Tagline to be used "Since 1977, Proven Results." Slideshow to be placed in the header or body of home page - please use stock real estate image.

Widgets: 1) Email Sign-up 2) Social media icons for FB and Workline 3) Featured Listings 4) Testimonials 5) Register button

Footer will have smaller company logo, attached logos and contact info:
Phone: (555) 261-0948 Mobile: (555) 718-3062
Email: mirelharrowgate@quellmail.example
Address: 58 E. Tamsin Avenue, Ste 410, Pensacola, FL 32599
Nice to have
• Use of a drop down menu:
Auctions-
1) Upcoming Auctions
2) Past Auctions

```html
<!DOCTYPE html>
<html lang="en">
<head>
<meta charset="utf-8">
<title>Harrowgate Auctions</title>
<link href="https://fonts.googleapis.com/css2?family=Arimo:ital,wght@0,400;0,700;1,400&family=Open+Sans:wght@400;600;700&family=Raleway:wght@700&display=swap" rel="stylesheet">
<style>
:root{
  --navy:#23238f;
  --navy-deep:#000066;
  --red:#b10000;
  --dark:#333333;
  --footer:#232323;
  --panel:#efefef;
  --text:#222222;
  --muted:#555555;
}
*{box-sizing:border-box;margin:0;padding:0}
html,body{width:980px;height:1200px;overflow:hidden;background:#fff}
body{position:relative;font-family:Arimo,Arial,sans-serif;color:var(--text)}
.abs{position:absolute}

/* header */
.brand{left:107px;top:26px;display:flex;align-items:center;gap:10px}
.brand-square{width:52px;height:52px;background:var(--navy-deep)}
.brand-name{font-family:"Open Sans",sans-serif;font-weight:700;font-size:25px;line-height:26px;color:var(--navy-deep)}
.connect{left:608px;top:62px;font-family:"Open Sans",sans-serif;font-weight:600;font-size:18px;color:#3a3a3a;letter-spacing:.5px}
.social{top:55px;width:32px;height:37px;border:1px solid #ddd;background:#f4f4f4;font-size:6px;color:#333;text-align:center;padding-top:29px}
.social.one{left:781px}.social.two{left:825px}
.social::before{content:"";position:absolute;left:3px;top:3px;width:24px;height:24px;background:var(--navy)}

/* nav */
.nav{left:0;top:112px;width:980px;height:41px;background:var(--navy)}
.nav ul{list-style:none;display:flex;position:absolute;left:86px;top:0;height:41px}
.nav li{color:#fff;font-family:"Open Sans",sans-serif;font-weight:600;font-size:11.5px;line-height:41px;padding:0 14px;position:relative}
.nav li+li::before{content:"";position:absolute;left:0;top:8px;height:26px;border-left:1px solid rgba(255,255,255,.35)}

/* hero */
.hero-band{left:0;top:153px;width:980px;height:298px;background:var(--red)}
.hero-photo{left:91px;top:165px;width:548px;height:270px;background:linear-gradient(180deg,#d3d6d8 0%,#b9aca0 45%,#7d5d4e 70%,#5f6a4c 100%)}
.tag-strip{left:125px;top:378px;width:431px;height:57px;background:rgba(60,60,60,.55)}
.tagline{left:142px;top:392px;font-family:Raleway,sans-serif;font-weight:700;font-size:27px;color:#fff;text-shadow:0 1px 2px rgba(0,0,0,.5)}
.dropdown{left:156px;top:163px;width:131px;border-radius:3px;overflow:hidden;box-shadow:0 2px 4px rgba(0,0,0,.3)}
.dropdown div{height:28px;line-height:28px;padding-left:14px;font-size:12px;color:#fff;font-family:"Open Sans",sans-serif}
.dropdown .on{background:var(--red)}
.dropdown .off{background:var(--navy)}
.signup{left:639px;top:165px;width:248px;height:270px;background:var(--dark)}
.signup h2{position:absolute;left:24px;top:14px;font-family:"Open Sans",sans-serif;font-weight:400;font-size:19px;color:#fff}
.field{position:absolute;left:24px;width:187px;height:28px;background:linear-gradient(#fff,#ececec);font-size:11px;color:#555;line-height:28px;padding-left:8px}
.field.n{top:60px}.field.e{top:107px}
.subscribe{position:absolute;left:25px;top:153px;width:80px;height:27px;background:var(--red);border-radius:3px;color:#fff;font-family:"Open Sans",sans-serif;font-weight:700;font-size:13px;text-align:center;line-height:27px}
.register{position:absolute;left:0;bottom:0;width:248px;height:43px;background:linear-gradient(#3a3a3a,#000);border-top:1px solid #555;color:#fff;font-family:"Open Sans",sans-serif;font-weight:700;font-size:16px;line-height:42px;text-align:right;padding-right:22px;letter-spacing:.5px}

/* sections */
.heading{font-family:"Open Sans",sans-serif;font-size:19px;font-weight:400;color:var(--red)}
.heading.strong{font-weight:700}
.card{left:97px;width:504px;height:229px;background:var(--panel)}
.card-photo{position:absolute;left:11px;top:15px;width:187px;height:156px}
.btn{position:absolute;top:185px;height:24px;color:#fff;font-size:13px;line-height:24px;padding-left:27px}
.btn.details{left:11px;width:80px;background:#222}
.btn.gallery{left:110px;width:88px;background:var(--navy-deep)}
.btn svg{position:absolute;left:7px;top:5px}
.info{position:absolute;left:210px;width:282px;background:#fff;border:1px solid #ddd;border-radius:3px;padding:10px 8px}
.info.top{top:13px;height:76px}
.info.low{top:104px;height:116px}
.info h3{font-weight:400;font-size:12.5px;color:var(--red);margin-bottom:6px}
.info p{font-size:11px;line-height:16px;color:#333}
.info .small{font-size:9.5px;line-height:12px}
.info .label{font-weight:700;font-size:10.5px;margin-top:10px;line-height:12px}
.feature{left:626px;top:523px;width:258px;height:209px;background:var(--panel);padding:17px 16px}
.feature h4{font-size:11.5px;font-weight:700;color:#333}
.feature-photo{margin-top:8px;width:217px;height:97px;background:linear-gradient(180deg,#5e7d3a 0%,#9a9688 40%,#b9b3a4 60%,#a8574b 85%,#6e9440 100%)}
.feature p{font-size:10px;line-height:15px;color:#333;margin-top:10px}
.feature p+p{margin-top:4px;font-size:11px}
.quote{left:626px;top:789px;width:258px;height:208px;background:var(--panel);padding:36px 14px 0 20px}
.quote p{font-style:italic;font-size:10.6px;line-height:16.4px;color:#555;text-indent:18px}
.quote .mark{position:absolute;font-size:22px;color:#bbb;font-family:Georgia,serif}
.quote cite{position:absolute;right:26px;top:184px;color:var(--red);font-size:12px}

/* footer */
.footer{left:0;top:1029px;width:980px;height:138px;background:var(--footer)}
.contact{position:absolute;left:87px;top:30px;font-size:11.3px;line-height:18px;color:#eee}
.contact b{color:#fff}
.badge{position:absolute;background:#8a8a8a;border-radius:3px}
.foot-brand{position:absolute;left:725px;top:69px;display:flex;align-items:center;gap:10px}
.foot-brand .sq{width:42px;height:42px;background:#9a9a9a}
.foot-brand span{font-family:"Open Sans",sans-serif;font-weight:700;font-size:18px;line-height:19px;color:#a9a9a9}
.copy{left:0;top:1167px;width:980px;height:33px;background:var(--navy);color:#fff;font-size:11.5px;text-align:center;line-height:33px}
.copy u{text-underline-offset:2px}
</style>
</head>
<body>

<header>
  <div class="abs brand">
    <div class="brand-square"></div>
    <div class="brand-name">Harrowgate<br>Auctions</div>
  </div>
  <div class="abs connect">STAY CONNECTED:</div>
  <div class="abs social one">Friendline</div>
  <div class="abs social two">Workline</div>
</header>

<nav class="abs nav">
  <ul>
    <li>HOME</li><li>AUCTIONS</li><li>ONLINE AUCTIONS</li><li>ABOUT US</li><li>SERVICES</li><li>REAL ESTATE LISTINGS</li><li>REFERENCES</li><li>CONTACT US</li>
  </ul>
</nav>

<section class="abs hero-band"></section>
<div class="abs hero-photo" role="img" aria-label="Two-storey brick and siding family home with a covered porch and garage"></div>
<div class="abs tag-strip"></div>
<div class="abs tagline">SINCE 1977, PROVEN RESULTS</div>
<div class="abs dropdown">
  <div class="on">Upcoming Auctions</div>
  <div class="off">Past Auctions</div>
</div>
<aside class="abs signup">
  <h2>Email sign-up</h2>
  <div class="field n">Name</div>
  <div class="field e">Email</div>
  <div class="subscribe">Subscribe</div>
  <div class="register">REGISTER NOW! &nbsp;&gt;&gt;</div>
</aside>

<h2 class="abs heading strong" style="left:100px;top:484px">UPCOMING AUCTIONS</h2>

<article class="abs card" style="top:523px">
  <div class="card-photo" role="img" aria-label="Grey-roofed suburban house with landscaped front garden" style="background:linear-gradient(180deg,#e8ecef 0%,#8d8f8c 45%,#6d6a60 70%,#5b7a3a 100%)"></div>
  <div class="btn details"><svg width="12" height="12" viewBox="0 0 12 12"><circle cx="5" cy="5" r="3.5" fill="none" stroke="#ddd" stroke-width="1.5"/><line x1="7.5" y1="7.5" x2="11" y2="11" stroke="#ddd" stroke-width="1.8"/></svg>Details</div>
  <div class="btn gallery"><svg width="15" height="13" viewBox="0 0 15 13"><rect x="1" y="1" width="9" height="8" fill="none" stroke="#fff" stroke-width="1.4"/><rect x="5" y="4" width="9" height="8" fill="var(--navy-deep)" stroke="#fff" stroke-width="1.4"/></svg>Gallery</div>
  <div class="info top"><h3>Auction 1</h3><p>Lorem Ipsum is simply dummy text of the printing and typesetting industry.</p></div>
  <div class="info low"><h3>Online Bidding Only</h3><p class="small">Began:&nbsp; Friday, May 24, 2013 at 10:06 AM EDT</p><p class="label">Location</p><p class="small">2716 Orrin Ln. NW Kessford, IA 50999</p></div>
</article>

<article class="abs card" style="top:769px">
  <div class="card-photo" role="img" aria-label="Beige two-storey house with white balconies and lawn" style="background:linear-gradient(180deg,#9fb6d8 0%,#c9b08c 45%,#a88c6c 70%,#5f8a3a 100%)"></div>
  <div class="btn details"><svg width="12" height="12" viewBox="0 0 12 12"><circle cx="5" cy="5" r="3.5" fill="none" stroke="#ddd" stroke-width="1.5"/><line x1="7.5" y1="7.5" x2="11" y2="11" stroke="#ddd" stroke-width="1.8"/></svg>Details</div>
  <div class="btn gallery"><svg width="15" height="13" viewBox="0 0 15 13"><rect x="1" y="1" width="9" height="8" fill="none" stroke="#fff" stroke-width="1.4"/><rect x="5" y="4" width="9" height="8" fill="var(--navy-deep)" stroke="#fff" stroke-width="1.4"/></svg>Gallery</div>
  <div class="info top"><h3>Auction 1</h3><p>Lorem Ipsum is simply dummy text of the printing and typesetting industry.</p></div>
  <div class="info low"><h3>Online Bidding Only</h3><p class="small">Began:&nbsp; Friday, May 24, 2013 at 10:06 AM EDT</p><p class="label">Location</p><p class="small">2716 Orrin Ln. NW Kessford, IA 50999</p></div>
</article>

<h2 class="abs heading" style="left:625px;top:484px">FEATURED LISTINGS</h2>
<aside class="abs feature">
  <h4>Multi Estate &amp; Consignment Auction</h4>
  <div class="feature-photo" role="img" aria-label="Cottage-style home with porch and flowering front garden"></div>
  <p><b>Start Date/ Time:</b> Saturday, April 13,<br>2013 At 10:00 Am</p>
  <p>Multi Estate &amp; Consignment Auction</p>
</aside>

<h2 class="abs heading" style="left:626px;top:754px">TESTIMONIALS</h2>
<aside class="abs quote">
  <span class="mark" style="left:16px;top:14px">&ldquo;</span>
  <p>Lorem Ipsum has been the industry's standard dummy text ever since the 1500s, when an unknown printer took a galley of type and scrambled it to make a type speci men book.It has survived not only five centuries, but also the leap into electronic typesetting, remaining essentially unchanged.</p>
  <span class="mark" style="left:92px;top:163px">&rdquo;</span>
  <cite>Marla Penfold</cite>
</aside>

<footer class="abs footer">
  <div class="contact">
    <b>Phone:</b> (555) 261-0948<br>
    <b>Mobile:</b> (555) 718-3062<br>
    <b>Email:</b> mirelharrowgate@quellmail.example<br>
    <b>Address:</b> 58 E. Tamsin Avenue,<br>Ste 410, Pensacola, FL 32599
  </div>
  <div class="badge" style="left:330px;top:36px;width:46px;height:34px"></div>
  <div class="badge" style="left:384px;top:36px;width:28px;height:34px"></div>
  <div class="badge" style="left:421px;top:34px;width:114px;height:36px"></div>
  <div class="badge" style="left:545px;top:33px;width:72px;height:36px"></div>
  <div class="badge" style="left:347px;top:86px;width:142px;height:32px"></div>
  <div class="badge" style="left:505px;top:88px;width:96px;height:28px"></div>
  <div class="foot-brand"><div class="sq"></div><span>Harrowgate<br>Auctions</span></div>
</footer>
<div class="abs copy">Copyright © 2014 <u>Harrowgate Auctions</u> All Rights Reserved.</div>

</body>
</html>
```